LEARN Business Skills so you can Earn a good living

size of the poster is 8”x 10.75" plus 0.25" bleed.
Please leave 1 inch on the bottoum for footer
I want a design a poster that will attract people's attention.
I appreciate a creative ad however the ad should not take away from being able to clearly read the text.
-I also appreciate a simple creative ad that is not too busy.
-you can use graphics, vectors, or pictures of real people.
-however, if you use real people it should be a white male that is wearing a white shirt and look like a professional person.

Target Market(s)

Potential young business people

Industry/Entity Type

education

Requirements
Must have
• easy to read the text
Nice to have
• I would like a "creative" simple ad that is easy to be read
Should not have
• pictures of women

```html
<!DOCTYPE html>
<html lang="en">
<head>
<meta charset="utf-8">
<title>Learn It To Earn It – Business Enrichment Course</title>
<link href="https://fonts.googleapis.com/css2?family=Poppins:wght@300;400;500;600;700;800&display=swap" rel="stylesheet">
<style>
  :root {
    --stage: #d9d9d9;
    --paper: #ffffff;
    --ink: #1e1e1e;
    --band: #222222;
    --frame: #cfcfcf;
    --icon-bg: #6b6b6b;
    --rule: #bdbdbd;
    --accent: #1f3f9a;
  }
  * { margin: 0; padding: 0; box-sizing: border-box; }
  html, body { width: 1200px; height: 1200px; overflow: hidden; }
  body { background: var(--stage); font-family: "Poppins", sans-serif; color: var(--ink); position: relative; }

  .poster {
    position: absolute; left: 178px; top: 38px;
    width: 1360px; height: 1813px;
    transform: scale(0.62); transform-origin: top left;
    background: var(--paper); overflow: hidden;
  }
  .hero-backdrop {
    position: absolute; left: 0; top: 0; width: 1360px; height: 1124px;
    background: linear-gradient(180deg, #ffffff 0%, #f4f4f4 35%, #e2e2e2 100%);
  }
  .hero-photo {
    position: absolute; left: 590px; top: 260px; width: 770px; height: 864px;
    background: radial-gradient(ellipse at 55% 55%, #4a4d57 0%, #3a3b42 40%, #9a9a9a 75%, #dcdcdc 100%);
    border-radius: 40px 0 0 0;
  }
  .headline { position: absolute; left: 84px; top: 110px; font-size: 202px; line-height: 182px; }
  .headline .strong { font-weight: 800; letter-spacing: -5px; }
  .headline .light { font-weight: 300; letter-spacing: 2px; }
  .rule { position: absolute; left: 87px; top: 499px; width: 757px; height: 2px; background: var(--rule); }
  .course-title { position: absolute; left: 84px; top: 560px; font-size: 80px; line-height: 80px; font-weight: 700; letter-spacing: 2px; }
  .since { position: absolute; left: 86px; top: 860px; font-size: 42px; font-weight: 700; }
  .mode { position: absolute; left: 86px; top: 948px; font-size: 42px; font-weight: 700; }

  .benefits-band { position: absolute; left: 0; top: 1124px; width: 1360px; height: 506px; background: var(--band); }
  .benefits-frame {
    position: absolute; left: 92px; top: 1185px; width: 1176px; height: 272px;
    border: 2px solid var(--frame); border-radius: 32px;
  }
  .benefits-title {
    position: absolute; left: 165px; top: 1152px; width: 1030px; height: 78px;
    background: var(--paper); border-radius: 32px;
    font-size: 46px; font-weight: 700; text-align: center; line-height: 78px;
  }
  .benefit-divider { position: absolute; top: 1255px; width: 2px; height: 185px; background: #3d3d3d; }
  .benefit { position: absolute; top: 1262px; width: 400px; text-align: center; color: var(--paper); }
  .benefit svg { display: block; margin: 0 auto 18px; }
  .benefit-label { font-size: 33px; font-weight: 800; }

  .topics {
    position: absolute; left: 40px; top: 1488px; width: 1280px;
    color: var(--paper); text-align: center; font-size: 20.5px; font-weight: 300; line-height: 25px;
  }

  .footer { position: absolute; left: 0; top: 1630px; width: 1360px; height: 183px; }
  .brand { position: absolute; left: 95px; top: 28px; width: 200px; text-align: center; }
  .brand-name { display: flex; align-items: center; justify-content: center; gap: 10px; font-size: 36px; font-weight: 400; color: var(--accent); }
  .brand-name .dot { width: 24px; height: 24px; border-radius: 50%; background: var(--accent); flex: none; }
  .brand-sub { margin-top: 12px; font-size: 24px; font-weight: 400; }
  .footer-divider { position: absolute; top: 20px; height: 110px; border-left: 2px dashed #aaa; }
  .contact { position: absolute; left: 348px; top: 14px; font-size: 24px; line-height: 42px; }
  .contact b { font-weight: 700; }
  .contact .note { font-size: 19px; }
  .contact .note b { font-weight: 500; }
  .sponsor { position: absolute; left: 1064px; top: 14px; }
  .sponsor-label { font-size: 22px; }
  .sponsor-name { display: flex; align-items: center; gap: 10px; margin-top: 10px; font-size: 23px; line-height: 26px; font-weight: 600; color: var(--accent); }
  .sponsor-name .square { width: 40px; height: 60px; background: var(--accent); flex: none; }
</style>
</head>
<body>
  <div class="poster">
    <div class="hero-backdrop" role="img" aria-label="Softly blurred bright office interior"></div>
    <div class="hero-photo" role="img" aria-label="Smiling businessman in dark suit, white shirt and blue tie seated at a desk with papers and keyboard"></div>

    <h1 class="headline"><span class="strong">LEARN</span> <span class="light">IT TO</span><br><span class="strong">EARN</span> <span class="light">IT</span></h1>
    <div class="rule"></div>
    <h2 class="course-title">BUSINESS<br>ENRICHMENT<br>COURSE</h2>
    <p class="since">since 2005</p>
    <p class="mode">In-person/Remote</p>

    <div class="benefits-band"></div>
    <div class="benefits-frame"></div>
    <div class="benefits-title">A PROVEN SUCCESS OF HELPING PEOPLE</div>
    <div class="benefit-divider" style="left:440px"></div>
    <div class="benefit-divider" style="left:864px"></div>

    <div class="benefit" style="left:74px">
      <svg width="96" height="96" viewBox="0 0 96 96"><circle cx="48" cy="48" r="46" fill="var(--icon-bg)" stroke="#eee" stroke-width="2"/><g fill="none" stroke="#fff" stroke-width="2.5"><rect x="30" y="24" width="36" height="26" rx="3"/><circle cx="48" cy="52" r="11"/><path d="M41 61l-5 12 7-3 4 5 1-11M55 61l5 12-7-3-4 5"/></g></svg>
      <div class="benefit-label">Get a quality job</div>
    </div>
    <div class="benefit" style="left:452px">
      <svg width="96" height="96" viewBox="0 0 96 96"><circle cx="48" cy="48" r="46" fill="var(--icon-bg)" stroke="#eee" stroke-width="2"/><g fill="none" stroke="#fff" stroke-width="2.5"><rect x="24" y="56" width="8" height="12"/><rect x="36" y="50" width="8" height="18"/><rect x="48" y="44" width="8" height="24"/><rect x="60" y="36" width="8" height="32"/><path d="M22 46l14-8 10 4 22-14M62 27h7v7"/></g></svg>
      <div class="benefit-label">Start/grow a business</div>
    </div>
    <div class="benefit" style="left:865px">
      <svg width="96" height="96" viewBox="0 0 96 96"><circle cx="48" cy="48" r="46" fill="var(--icon-bg)" stroke="#eee" stroke-width="2"/><g fill="none" stroke="#fff" stroke-width="2.5"><rect x="36" y="46" width="36" height="20" rx="2"/><circle cx="54" cy="56" r="5"/><path d="M22 54h12M22 60h12M22 66h12M24 40l12-8 8 4 16-10M54 26h7v7"/></g></svg>
      <div class="benefit-label">Increase their salary</div>
    </div>

    <p class="topics">
      BUSINESS ADMINISTRATION &nbsp;• SMALL BUSINESS MANAGEMENT &nbsp;• FINANCE &nbsp;• INVESTMENTS &nbsp;• COMPUTERS &nbsp;• ACCOUNTING<br>
      SALES &nbsp;• MARKETING &nbsp;• PROJECT MANAGEMENT • INTERVIEWING SKILLS • BUSINESS LAW &nbsp;• NEGOTIATION &nbsp;• PUBLIC SPEAKING<br>
      IMPORT/EXPORT • INFORMATION TECHNOLOGY • DISTRIBUTION &nbsp;• MARKETING &nbsp;• BOOKKEEPING &nbsp;• REAL ESTATE<br>
      HEALTH CARE-MANAGEMENT &nbsp;• E-COMMERCE • DIGITAL MARKETING • HUMAN RESOURCES
    </p>

    <footer class="footer">
      <div class="brand">
        <div class="brand-name"><span class="dot"></span>Northway</div>
        <div class="brand-sub">Career Network</div>
      </div>
      <div class="footer-divider" style="left:310px"></div>
      <div class="contact">
        <div><b>Call:</b> 555 210 4800 x 212</div>
        <div><b>Email:</b> info@northwaycareers.org</div>
        <div class="note">Northway is sponsored in part by the <b>Harlan Brookfield Foundation</b></div>
      </div>
      <div class="footer-divider" style="left:1030px"></div>
      <div class="sponsor">
        <div class="sponsor-label">Sponsored in part</div>
        <div class="sponsor-name"><span class="square"></span><span>Bridgewell<br>Health Partners</span></div>
      </div>
    </footer>
  </div>
</body>
</html>
```